Create website for home automation - Control your lighting, fans, blinds etc remotely by smartphone

Plan for SHOPIFY Website - Our Clever Dwelling
Company name: Our Clever Dwelling
Company Slogan: Calm Evenings Come Naturally
Clean, Modern, Easy to Navigate, easy to maintain - not a lot of coding. We need flash technology but displaying simply what we do.
What we provide:
We will be offering wireless switch which can be added to iOS/Android App via WiFi, allowing users to remotely turn on/off connected lights, fans, security cameras, appliances, irrigation, humidifier separately from anywhere at any time.
Control your home away from home. No more wandering of your mind on those lights or appliances which you might have left switched on. No need to drive back home to check and switch them off. Save that energy, money and time just with a click of your phone no matter how far you are from home.
Replace your home electrical switches with smart switches. They retrofit existing electrical switches and allow you to make the transformation as needed.
Easy to use and intuitive app allows you to control your lights and devices just at a click. Set any kind of ambiance suiting your occasion.
Set scenes in smartphone app to group and operate your devices just at a button click. Same device can be included in more than one scene.
Collections and Products
Light Switches
Wall Plugs
Fan Switch
Pendants etc special lighting types.
Light Dimmers
Blind Controllers
Home Page:
Home page needs to telling customers what we do and how we do it in a few words to grab people.
Phone
Email
Support – Download instructions per product
Client login
Wholesale login
Promotional video to be on home screen - this is a short 1.5 - 2 min illustration introduction video to who we are and what we do - this is yet to be created)
Social media link - Friendbook
Pages:
FAQ
About Us
Support/Shipping/Returns policy
Support/Installation
Blog posts
Product pages:
Description
Price
Space for where a video will be featured - how each product works/installation.
Reviews
Our competition:
http://www.brivo.com.au
https://lumigardenhub.com.au/2018/04/05/best-smart-light-switches-and-plugs/
https://www.tavelinq.com

```html
<!DOCTYPE html>
<html lang="en">
<head>
<meta charset="utf-8">
<title>Our Clever Dwelling — Calm Evenings Come Naturally</title>
<link rel="stylesheet" href="https://fonts.googleapis.com/css2?family=Poppins:wght@400;500;600;700&family=Mulish:wght@400;600;700&display=swap">
<style>
:root{
  --blue:#1f6cbf;
  --blue-dark:#175aa6;
  --navy:#0e2670;
  --navy-deep:#0c1f5e;
  --ink:#17246a;
  --text:#2a2a2a;
  --white:#ffffff;
  --hero-a:#6f6152;
  --hero-b:#c9b79c;
}
*{margin:0;padding:0;box-sizing:border-box}
html,body{width:1200px;height:3922px;overflow:hidden}
body{font-family:"Mulish",sans-serif;color:var(--text);background:var(--white);position:relative}
section,header,footer{position:absolute;left:0;width:1200px}
.heading{font-family:"Poppins",sans-serif;font-weight:700;text-transform:uppercase}
.photo{position:absolute}
.body-copy{font-size:16px;line-height:31px}
.link-row{display:flex;gap:44px;font-family:"Poppins",sans-serif;font-weight:600;font-size:17px;text-transform:uppercase}

/* hero */
.hero{top:0;height:672px;overflow:hidden}
.hero .photo{inset:0;background:linear-gradient(115deg,#4d5560 0%,var(--hero-a) 35%,var(--hero-b) 70%,#8c7a66 100%)}
.nav{position:absolute;top:26px;left:88px;right:88px;display:flex;align-items:center}
.brand{display:flex;align-items:center;gap:10px;color:var(--white);font-family:"Poppins",sans-serif;font-weight:600;font-size:16px;text-transform:uppercase}
.brand-mark{width:26px;height:26px;border:3px solid var(--white)}
.menu{display:flex;gap:30px;margin-left:52px;color:var(--white);font-family:"Poppins",sans-serif;font-size:16px}
.logins{margin-left:auto;display:flex;gap:24px}
.logins a{border:2px solid var(--white);color:var(--white);padding:5px 12px;font-family:"Poppins",sans-serif;font-size:16px;text-decoration:none}
.hero-title{position:absolute;right:88px;top:305px;color:var(--white);text-align:right}
.hero-title h1{font-size:49px;letter-spacing:.5px}
.hero-title p{font-family:"Poppins",sans-serif;font-size:35px;margin-top:6px}

/* what we do */
.what{top:672px;height:481px}
.what .photo{left:105px;top:86px;width:475px;height:314px;background:linear-gradient(135deg,#2e5f9e,#bfc6d0 55%,#eaeaea)}
.what-text{position:absolute;left:627px;top:88px;width:470px}
.what-text h2{font-size:33px;color:var(--ink);margin-bottom:14px}
.what-text .link-row{color:var(--blue);margin-top:24px}

/* how we do it */
.how{top:1153px;height:483px;background:var(--blue);color:var(--white)}
.how-text{position:absolute;left:105px;top:84px;width:490px}
.how-text h2{font-size:33px;margin-bottom:14px}
.how-text .link-row{margin-top:30px}
.how .photo{left:630px;top:83px;width:478px;height:317px;border:6px solid var(--white);background:linear-gradient(135deg,#9aa4ad,#e3e6ea 50%,#6d7a86)}

/* video */
.video{top:1636px;height:481px;overflow:hidden}
.video .photo{inset:0;background:linear-gradient(100deg,#9b9a98 0%,#7a746d 45%,#4c4843 62%,#c9b9a3 100%)}
.video-caption{position:absolute;left:0;right:0;top:176px;text-align:center;color:var(--white)}
.video-caption h2{font-size:27px}
.play{display:inline-flex;align-items:center;gap:8px;margin-top:20px;font-family:"Poppins",sans-serif;font-weight:600;font-size:26px;text-transform:uppercase}

/* features */
.features{top:2117px;height:301px;display:flex;justify-content:center;gap:66px;padding-top:65px}
.feature{width:287px;text-align:center}
.feature svg{display:block;margin:0 auto}
.feature h3{font-family:"Poppins",sans-serif;font-weight:500;font-size:24px;color:var(--blue);margin:14px 0 8px}
.feature p{font-size:15px;line-height:25px}

/* product */
.product{top:2418px;height:580px;background:var(--navy);color:var(--white)}
.product .photo{left:110px;top:99px;width:470px;height:390px;background:radial-gradient(circle at 50% 85%,#5fb3f0,#1c3f80 55%,#0d1c45)}
.product-info{position:absolute;left:612px;top:80px;width:430px}
.product-info h2{font-family:"Poppins",sans-serif;font-weight:700;font-size:36px}
.price{font-family:"Poppins",sans-serif;font-weight:600;font-size:17px;margin-top:10px}
.price s{margin-right:8px}
.cart{display:flex;gap:29px;margin-top:28px}
.qty{width:125px;height:32px;background:var(--white);color:var(--text);display:flex;align-items:center;justify-content:center;font-size:15px}
.add{width:269px;height:32px;background:var(--blue);display:flex;align-items:center;justify-content:center;font-family:"Poppins",sans-serif;font-size:14px;text-transform:uppercase}
.product-info .body-copy{font-size:15px;line-height:25px;margin-top:21px}

/* gallery */
.gallery{top:2998px;height:335px;text-align:center}
.gallery h2{font-family:"Poppins",sans-serif;font-weight:500;font-size:36px;color:var(--blue);margin-top:27px}
.tiles{display:flex;justify-content:center;gap:8px;margin-top:20px}
.tile{position:relative;width:251px;height:196px}
.tile.t1{background:linear-gradient(135deg,#2c5795,#cfd4da)}
.tile.t2{background:linear-gradient(135deg,#b89d7e,#e7ddd0)}
.tile.t3{background:linear-gradient(135deg,#8e97a0,#e2e5e8)}
.tile.t4{background:linear-gradient(135deg,#d9d2c6,#8fb3a1)}

/* newsletter */
.newsletter{top:3333px;height:254px;background:var(--blue-dark);color:var(--white);text-align:center}
.newsletter h2{font-size:35px;font-weight:600;margin-top:32px}
.newsletter p{font-family:"Poppins",sans-serif;font-weight:500;font-size:18px;margin-top:12px}
.signup{display:flex;justify-content:center;gap:15px;margin-top:32px}
.email{width:353px;height:57px;border-radius:29px;background:var(--white);color:#9a9a9a;font-size:14px;display:flex;align-items:center;padding-left:28px}
.subscribe{width:262px;height:57px;border-radius:29px;background:var(--navy-deep);display:flex;align-items:center;justify-content:center;font-family:"Poppins",sans-serif;font-weight:600;font-size:17px;text-transform:uppercase}

/* footer */
.footer{top:3587px;height:335px;background:var(--navy-deep);color:var(--white)}
.col{position:absolute;top:40px}
.col h4{font-family:"Poppins",sans-serif;font-weight:600;font-size:15px;text-transform:uppercase;margin-bottom:18px}
.col li{list-style:none;font-size:15px;line-height:31.5px;display:flex;align-items:center;gap:10px}
.dot{width:9px;height:9px;background:var(--white);border-radius:50%}
.spread p{font-size:13px;margin-bottom:24px}
.badges{display:flex;gap:10px}
.badges span{height:36px;padding:0 18px;border-radius:18px;display:flex;align-items:center;font-size:14px;font-weight:600}
.b1{background:#3b5fbf}.b2{background:#3aa3e6}.b3{background:#d9473b}
.copyright{position:absolute;left:175px;top:252px;font-size:15px}
</style>
</head>
<body>

<header class="hero">
  <div class="photo" role="img" aria-label="Hand holding a smartphone with a home control app in front of a bright living room"></div>
  <nav class="nav">
    <div class="brand"><span class="brand-mark"></span>Our Clever Dwelling</div>
    <div class="menu"><span>Home</span><span>Product</span><span>FAQ</span><span>About Us</span><span>Installation</span><span>Blog posts</span></div>
    <div class="logins"><a>Client login</a><a>Wholesale login</a></div>
  </nav>
  <div class="hero-title">
    <h1 class="heading">Our Clever Dwelling</h1>
    <p>Calm Evenings Come Naturally</p>
  </div>
</header>

<section class="what">
  <div class="photo" role="img" aria-label="Smartwatch showing home controls in front of a tablet dashboard"></div>
  <div class="what-text">
    <h2 class="heading">What we do</h2>
    <p class="body-copy">Sed ut perspiciatis unde omnis iste natus error sit voluptatem accusantium doloremque laudantium, totam rem aperiam, eaque ipsa quae ab illo inventore veritatis et quasi architecto beatae vitae dicta sunt explicabo. Nemo enim ipsam voluptatem quia voluptas sit aspernatur aut odit aut fugit, sed quia consequuntur magni dolores eos qui ratione voluptatem sequi nesciunt.</p>
    <div class="link-row"><span>View details</span></div>
  </div>
</section>

<section class="how">
  <div class="how-text">
    <h2 class="heading">How we do it</h2>
    <p class="body-copy">Sed ut perspiciatis unde omnis iste natus error sit voluptatem accusantium doloremque laudantium, totam rem aperiam, eaque ipsa quae ab illo inventore veritatis et quasi architecto beatae vitae dicta sunt explicabo. Nemo enim ipsam voluptatem quia voluptas sit aspernatur aut odit aut fugit, sed quia consequuntur magni dolores eos qui ratione voluptatem sequi nesciunt.</p>
    <div class="link-row"><span>View details</span><span>Download instructions</span></div>
  </div>
  <div class="photo" role="img" aria-label="Phone controlling connected devices in a modern kitchen"></div>
</section>

<section class="video">
  <div class="photo" role="img" aria-label="Wall-mounted smart home touch panel beside a living room"></div>
  <div class="video-caption">
    <h2 class="heading">Sed ut perspiciatis unde omnis iste natus</h2>
    <div class="play">
      <svg width="26" height="26" viewBox="0 0 26 26"><circle cx="13" cy="13" r="13" fill="#fff"/><path d="M10 7.5v11l9-5.5z" fill="#4c4843"/></svg>
      Play video
    </div>
  </div>
</section>

<section class="features">
  <div class="feature">
    <svg width="48" height="42" viewBox="0 0 48 42" fill="none" stroke="#1f6cbf" stroke-width="2.4"><rect x="3" y="10" width="40" height="29" rx="3"/><path d="M9 10 32 3l3 7"/><rect x="30" y="19" width="15" height="10" rx="2"/><circle cx="36" cy="24" r="1.6" fill="#1f6cbf"/></svg>
    <h3>Discount system</h3>
    <p>Nam libero tempore, cum soluta nobis est eligendi optio, cumque nihil impedit, quo minus</p>
  </div>
  <div class="feature">
    <svg width="40" height="46" viewBox="0 0 40 46" fill="none" stroke="#1f6cbf" stroke-width="2.4"><rect x="4" y="3" width="32" height="34" rx="5"/><path d="M4 22h32M4 11h32"/><circle cx="12" cy="29" r="2.2"/><circle cx="28" cy="29" r="2.2"/><path d="M10 37v6M30 37v6"/></svg>
    <h3>Free delivery</h3>
    <p>Nam libero tempore, cum soluta nobis est eligendi optio, cumque nihil impedit, quo minus</p>
  </div>
  <div class="feature">
    <svg width="50" height="42" viewBox="0 0 50 42" fill="none" stroke="#1f6cbf" stroke-width="2.4"><circle cx="18" cy="13" r="8"/><path d="M3 39c0-9 7-14 15-14s15 5 15 14z"/><circle cx="35" cy="10" r="6"/><path d="M33 21c8-1 14 4 14 12h-11"/></svg>
    <h3>Support 24/7</h3>
    <p>Nam libero tempore, cum soluta nobis est eligendi optio, cumque nihil impedit, quo minus</p>
  </div>
</section>

<section class="product">
  <div class="photo" role="img" aria-label="Glowing smart home control screen held above an open hand"></div>
  <div class="product-info">
    <h2>Our Product</h2>
    <div class="price"><s>$40.00</s>$35.00 Sale</div>
    <div class="cart"><div class="qty">1</div><div class="add">Add to cart</div></div>
    <p class="body-copy">Sed ut perspiciatis unde omnis iste natus error sit voluptatem accusantium doloremque laudantium, totam rem aperiam, eaque ipsa quae ab illo inventore veritatis et quasi architecto beatae vitae dicta sunt explicabo. Nemo enim ipsam voluptatem quia voluptas sit aspernatur.</p>
    <p class="body-copy">Sed ut perspiciatis unde omnis iste natus error sit voluptatem accusantium doloremque laudantium, totam rem aperiam, eaque ipsa quae ab illo inventore veritatis et quasi architecto beatae vitae dicta sunt explicabo. sequi nesciunt.</p>
  </div>
</section>

<section class="gallery">
  <h2>Snapgram</h2>
  <div class="tiles">
    <div class="tile t1" role="img" aria-label="Smartwatch with home controls"></div>
    <div class="tile t2" role="img" aria-label="Phone app in a warm living room"></div>
    <div class="tile t3" role="img" aria-label="Phone controlling kitchen devices"></div>
    <div class="tile t4" role="img" aria-label="Hands holding a tablet showing a home plan"></div>
  </div>
</section>

<section class="newsletter">
  <h2 class="heading">Newsletter</h2>
  <p>Sign up for 20% off your first online order.</p>
  <div class="signup"><div class="email">Your email address</div><div class="subscribe">Subscribe</div></div>
</section>

<footer class="footer">
  <div class="col" style="left:175px"><h4>Quick links</h4><ul><li>Home</li><li>Product</li><li>FAQ</li><li>About Us</li></ul></div>
  <div class="col" style="left:332px"><h4>Info</h4><ul><li>Support</li><li>Installation</li><li>Blog posts</li><li>Returns policy</li></ul></div>
  <div class="col" style="left:489px"><h4>Social</h4><ul><li><span class="dot"></span>Friendbook</li><li><span class="dot"></span>Chirper</li><li><span class="dot"></span>Pinboardly</li><li><span class="dot"></span>Snapgram</li></ul></div>
  <div class="col spread" style="left:698px"><h4>Help spread the word!</h4>
    <p>Please help us spread the news about our awesome products.</p>
    <div class="badges"><span class="b1">Friendbook</span><span class="b2">Chirper</span><span class="b3">Circleplus</span></div>
  </div>
  <div class="copyright">© 2018. All rights reserved.</div>
</footer>

</body>
</html>
```